Book cover - Lanterns Along the Winding Quay

Book cover for Ebook (Quillet) and wrap around print cover (Bindwell) (back, front, and spine)

The book title (may slightly change by end of brief):
(MAIN TITLE) 'Lanterns Along the Winding Quay'
(SUB HEADING) 'A Practical Seasonal Garden Companion for Planting Bulbs, Pruning Hedges and Growing Fresh Herbs'
by Dr Owen Pratchard

I would like a bold, stand out cover. Contemporary. I would like to avoid stereotypical images of people looking anxious or worried. I would like the design to be more uplifting and hopeful, rather than focusing on the negative aspect of anxiety, but avoiding cliched photos of people raising their hands in the air, smiling and jumping etc. The cover should appeal to both men and women.

Trim size of book cover (for BindWell) is 5.25" x 8" back and front with a spine size of 0.477 inches
Updates

Reason: I have decided to extend the deadline by 1 more day, not because I am unhappy with the quality of the designs, but because a few designers have contacted me to explain they have had technical difficulties when submitting their files. Thanks everyone for the hard work and great designs.

Target Market(s)

Males and females (16+) who struggle with social anxiety and shyness

Industry/Entity Type

Social

Font styles to use
Serif

Requirements
Must have
• Bold cover that is modern and contemporary. For example, I like these covers:
• http://lnkvo.test/7kTq3Wm
• http://lnkvo.test/9gHw5Ze
• http://lnkvo.test/4nVy8Kb
• http://lnkvo.test/6jFu2Xo
• http://lnkvo.test/3mEs9Lt
• http://lnkvo.test/8hGz4Nd
• http://lnkvo.test/5bJk7Pv
Nice to have
• Open to abstract designs.
Should not have
• No stereotypical pictures of people who look anxious or worried. Avoid cliched photos of people raising their hands in the air, smiling and jumping etc.

```html
<!DOCTYPE html>
<html lang="en">
<head>
<meta charset="utf-8">
<title>Lanterns Along the Winding Quay — Front Cover</title>
<link href="https://fonts.googleapis.com/css2?family=Marcellus&family=Arimo:wght@400;700&display=swap" rel="stylesheet">
<style>
  :root {
    --page-bg: #ffffff;
    --cover-black: #050505;
    --title-gold: #f2ea9c;
    --subtitle-blue: #7cc6ec;
    --subtitle-white: #f4f4f4;
    --author-ink: #0a0a0a;
    --art-blue: #4a4fc0;
    --art-violet: #8c3cc4;
    --art-magenta: #d63a92;
    --art-red: #d8403e;
    --art-orange: #e68a2a;
    --art-green: #3aa84a;
  }
  * { box-sizing: border-box; margin: 0; padding: 0; }
  html, body {
    width: 1200px;
    height: 1200px;
    overflow: hidden;
    background: var(--page-bg);
  }
  .stage {
    width: 1200px;
    height: 1200px;
    display: flex;
    align-items: center;
    justify-content: center;
  }
  .front-cover {
    position: relative;
    width: 722px;
    height: 1100px;
    background: var(--cover-black);
    overflow: hidden;
  }
  .cover-art {
    position: absolute;
    left: 0;
    right: 0;
    bottom: 0;
    height: 460px;
    background:
      linear-gradient(to bottom, var(--cover-black) 0%, rgba(5,5,5,0) 55%),
      linear-gradient(to right, var(--art-blue), var(--art-violet) 22%, var(--art-magenta) 42%, var(--art-red) 60%, var(--art-orange) 78%, var(--art-green));
  }
  .title-block {
    position: absolute;
    top: 118px;
    left: 0;
    right: 0;
    text-align: center;
    font-family: "Marcellus", serif;
    font-weight: 400;
    color: var(--title-gold);
    line-height: 1.05;
  }
  .title-lead { font-size: 84px; letter-spacing: 2px; }
  .title-middle { font-size: 48px; margin-top: 16px; letter-spacing: 1px; }
  .title-end { font-size: 58px; margin-top: 14px; }
  .subtitle {
    position: absolute;
    top: 470px;
    left: 0;
    right: 0;
    text-align: center;
  }
  .subtitle-text {
    display: inline-block;
    text-align: left;
    font-family: "Arimo", sans-serif;
    font-size: 20px;
    line-height: 1.45;
    color: var(--subtitle-white);
    letter-spacing: 1.4px;
  }
  .subtitle-lead {
    display: block;
    font-weight: 700;
    color: var(--subtitle-blue);
    letter-spacing: 0.2px;
    font-size: 21px;
  }
  .author {
    position: absolute;
    bottom: 62px;
    left: 0;
    right: 0;
    text-align: center;
    font-family: "Arimo", sans-serif;
    font-size: 29px;
    color: var(--author-ink);
  }
  .author-name { font-weight: 700; }
</style>
</head>
<body>
  <main class="stage">
    <section class="front-cover">
      <div class="cover-art" role="img" aria-label="Abstract burst of coloured powder in blue, violet, magenta, red, orange and green rising from the bottom of the cover"></div>

      <h1 class="title-block">
        <div class="title-lead">LANTERNS</div>
        <div class="title-middle">ALONG THE WINDING</div>
        <div class="title-end">QUAY</div>
      </h1>

      <p class="subtitle">
        <span class="subtitle-text">
          <span class="subtitle-lead">A Practical Seasonal Garden Companion</span>
          for Planting Bulbs, Pruning Hedges<br>
          and Growing Fresh Herbs
        </span>
      </p>

      <p class="author">by <span class="author-name">Dr Owen Pratchard</span></p>
    </section>
  </main>
</body>
</html>
```